The Wardrobe Sage needs a pricing flyer

Single page flyer for The Wardrobe Sage.
The Wardrobe Sage is a lead generation service exclusively for the custom closet industry.
You design quality closets we provide quality leads!
Value Points:
Leads for closet companies are exclusive with a first right of refusal. Meaning, if the closet company cannot handle all of the leads we can provide, we will sell the excess to other closet companies. We will never sell the same lead to two different closet companies.
Benefits:
Flat rate and easy to budget
Cancel at anytime
Choose from 3 types of leads
Lower cost compared to overall cost per lead from other sources
More leads allows hiring more designers
More leads grow the companies revenue
Less time managing other advertising models
3 service options.
$250 each
- We send you the lead
- You and your team set the appointment
- Setting the appointment is up to you
2. $275 each
- We send you the lead
- We guarantee the appointment
- Return unset appointments for a replacement
3. $375 each
- We are your call center
- We generate the lead
- We set the appointment
Contact:
The Wardrobe Sage
704-555-0183
leads@TheWardrobeSage.com

```html
<!DOCTYPE html>
<html lang="en">
<head>
<meta charset="utf-8">
<title>The Wardrobe Sage – Pricing Flyer</title>
<link href="https://fonts.googleapis.com/css2?family=Itim&family=Marcellus&family=Fira+Sans:wght@500&family=Fjalla+One&display=swap" rel="stylesheet">
<style>
  :root {
    --page-bg: #e4e3df;
    --paper: #f7f6f5;
    --brown: #9c5a26;
    --copper: #a8652e;
    --gold: #d9a03f;
    --panel: #4b4b4e;
    --ink: #3c3c3e;
    --rule: #8d8d8d;
    --white: #ffffff;
  }
  * { margin: 0; padding: 0; box-sizing: border-box; }
  html, body { width: 1200px; height: 900px; overflow: hidden; background: var(--page-bg); }
  body { position: relative; font-family: "Itim", "Trebuchet MS", sans-serif; }

  .flyer {
    position: absolute; left: 321px; top: 20px;
    width: 558px; height: 860px;
    background: var(--paper);
    box-shadow: 0 2px 8px rgba(0,0,0,.18);
    overflow: hidden;
  }
  .flyer__backdrop {
    position: absolute; inset: 0 0 0 0;
    background: linear-gradient(180deg, #f3f2f1 0%, #e9e8e7 45%, #f1efee 100%);
    opacity: .9;
  }

  .intro {
    position: absolute; left: 18px; top: 14px; width: 400px;
    color: var(--brown); font-size: 13.6px; line-height: 27px; letter-spacing: -.15px;
  }

  .brand {
    position: absolute; left: 402px; top: 40px; width: 146px;
    display: flex; align-items: center; gap: 6px;
    color: var(--copper); font-size: 19px; line-height: 21px;
  }
  .brand__dot { width: 10px; height: 10px; border-radius: 50%; background: var(--copper); flex: none; }

  .benefits { position: absolute; left: 18px; top: 146px; }
  .benefits__title { font-family: "Fjalla One", sans-serif; color: var(--ink); font-size: 15px; letter-spacing: .3px; margin-bottom: 6px; }
  .benefits__list { list-style: none; color: var(--brown); font-size: 14px; }
  .benefits__list li { height: 24.5px; line-height: 24.5px; display: flex; align-items: center; }
  .benefits__list li::before {
    content: ""; width: 14px; height: 2px; background: var(--rule); margin: 0 13px 0 2px; flex: none;
  }

  .section-title {
    position: absolute; left: 18px; top: 356px; width: 522px;
    display: flex; align-items: center; gap: 6px;
    font-family: "Marcellus", serif; font-size: 19px; color: var(--ink); letter-spacing: .6px;
  }
  .section-title::before, .section-title::after { content: ""; flex: 1; height: 1px; background: var(--rule); }

  .plan {
    position: absolute; background: var(--panel); color: var(--white);
    border-top: 3px solid var(--copper); border-bottom: 4px solid var(--copper);
  }
  .plan__price { color: var(--gold); font-size: 23px; line-height: 30px; }
  .plan__list { list-style: none; font-size: 15.5px; }
  .plan__list li { line-height: 24.5px; display: flex; align-items: center; }
  .plan__list li::before { content: ""; width: 7px; height: 7px; border-radius: 50%; background: var(--gold); margin-right: 8px; }
  .plan--basic { left: 0; top: 400px; width: 334px; height: 135px; padding: 12px 0 0 18px; border-right: 3px solid var(--copper); }
  .plan--basic .plan__price { margin-bottom: 2px; }
  .plan--guaranteed { left: 188px; top: 550px; width: 370px; height: 153px; padding: 12px 10px 0 0; text-align: right; border-left: 3px solid var(--copper); }
  .plan--guaranteed .plan__list li { justify-content: flex-end; }
  .plan--guaranteed .plan__list li::before { display: none; }
  .plan--guaranteed .plan__list li::after { content: ""; width: 7px; height: 7px; border-radius: 50%; background: var(--gold); margin-left: 8px; }
  .plan--full { left: 0; top: 719px; width: 256px; height: 124px; padding: 11px 0 0 18px; border-right: 3px solid var(--copper); }

  .photo { position: absolute; border: 3px solid var(--copper); }
  .photo--office { left: 345px; top: 402px; width: 213px; height: 131px;
    background: linear-gradient(90deg, #e9e4dd 0%, #cfc7bc 25%, #2f3644 45%, #2b3140 80%, #5a4c3a 100%); border-right: none; }
  .photo--closet { left: 0; top: 550px; width: 173px; height: 153px;
    background: linear-gradient(90deg, #d9d5cf 0%, #f2efeb 30%, #b7a593 55%, #ece8e3 75%, #c9b59c 100%); border-left: none; }

  .contact { position: absolute; right: 10px; top: 720px; text-align: right; }
  .contact__title { font-family: "Fjalla One", sans-serif; color: var(--copper); font-size: 18px; letter-spacing: 1.2px; margin-bottom: 8px; }
  .contact__name { font-family: "Fira Sans", sans-serif; font-weight: 500; color: #1f1f1f; font-size: 17px; line-height: 22px; }
  .contact__phone { font-family: "Fira Sans", sans-serif; font-weight: 500; color: #1f1f1f; font-size: 26px; line-height: 32px; letter-spacing: .5px; }
  .contact__email { font-family: "Fira Sans", sans-serif; font-weight: 500; color: #1f1f1f; font-size: 17.5px; line-height: 28px; }
</style>
</head>
<body>
  <main class="flyer">
    <div class="flyer__backdrop" role="img" aria-label="Faint line drawing of a walk-in closet with shelves, boxes and hanging clothes"></div>

    <p class="intro">
      Leads for closet companies are exclusive with a first right of refusal.<br>
      Meaning, if the closet company cannot handle all of the leads<br>
      we can provide, we will sell the excess to other closet companies.<br>
      We will never sell the same lead to two different closet companies.
    </p>

    <div class="brand"><span class="brand__dot"></span><span>The Wardrobe Sage</span></div>

    <section class="benefits">
      <h2 class="benefits__title">BENEFITS –</h2>
      <ul class="benefits__list">
        <li>Flat rate and easy to budget</li>
        <li>Cancel at anytime</li>
        <li>Choose from 3 types of leads</li>
        <li>Lower cost compared to overall cost per lead from other sources</li>
        <li>More leads allows hiring more designers</li>
        <li>More leads grow the companies revenue</li>
        <li>Less time managing other advertising models</li>
      </ul>
    </section>

    <h2 class="section-title">SERVICE OPTIONS</h2>

    <section class="plan plan--basic">
      <h3 class="plan__price">$250 Each</h3>
      <ul class="plan__list">
        <li>We send you the lead</li>
        <li>You and your team set the appointment</li>
        <li>Setting the appointment is up to you</li>
      </ul>
    </section>
    <div class="photo photo--office" role="img" aria-label="Photo of a home office with dark navy built-in cabinetry"></div>

    <div class="photo photo--closet" role="img" aria-label="Photo of a bright white walk-in closet with hanging clothes and shoe shelves"></div>
    <section class="plan plan--guaranteed">
      <h3 class="plan__price">$275 Each</h3>
      <ul class="plan__list">
        <li>We send you the lead</li>
        <li>You and your team set the appointment</li>
        <li>We guarantee the appointment</li>
        <li>Return unset appointments for a replacement</li>
      </ul>
    </section>

    <section class="plan plan--full">
      <h3 class="plan__price">$375 Each</h3>
      <ul class="plan__list">
        <li>We are your call center</li>
        <li>We generate the lead</li>
        <li>We set the appointment</li>
      </ul>
    </section>

    <section class="contact">
      <h2 class="contact__title">CONTACT DETAILS</h2>
      <p class="contact__name">The Wardrobe Sage</p>
      <p class="contact__phone">704-555-0183</p>
      <p class="contact__email">leads@TheWardrobeSage.com</p>
    </section>
  </main>
</body>
</html>
```